Verdant Systems Business Card

want the back of card to be blue- with the logo in the center
front of card- info plus logo (info being mailing address, email address, and website address )
4 different names with titles to have on cards
1) Calvin Borsted - Owner
2) Naomi Trelvik- Customer Relationship Specialist
3) Felix Andrade- Vice President of Sales
4) Owen Markby- Chief Technology Officer

Target Market(s)

tech company in the government/probation office industry

Industry/Entity Type

Government Office

Contact Information for Business Card

1) Calvin Borsted - Owner

Colors
0355a3
ffffff

Requirements
Must have
• back side should be blue, with the logo placed in the center
• front side needs to include both the logo, as well as company info (info should include website address, email address, and mailing address)

```html
<!DOCTYPE html>
<html lang="en">
<head>
<meta charset="utf-8">
<title>Verdant Systems – Business Card</title>
<link href="https://fonts.googleapis.com/css2?family=Noto+Serif:wght@400&family=Roboto:wght@300;400&display=swap" rel="stylesheet">
<style>
  :root {
    --page-bg: #e4e1dc;
    --card-bg-top: #f6f6f5;
    --card-bg-bottom: #ebebea;
    --navy: #1d2b59;
    --text-grey: #6b6d72;
    --stripe-grey: #a3a5ab;
    --white: #ffffff;
  }
  * { margin: 0; padding: 0; box-sizing: border-box; }
  html, body {
    width: 1200px;
    height: 1054px;
    overflow: hidden;
    background: var(--page-bg);
  }
  .business-card {
    position: absolute;
    left: 100px;
    top: 225px;
    width: 1000px;
    height: 604px;
    background: linear-gradient(180deg, var(--card-bg-top), var(--card-bg-bottom));
    box-shadow: 0 10px 30px rgba(0, 0, 0, 0.12);
    overflow: hidden;
  }
  .card-band {
    position: absolute;
    left: 0;
    top: 0;
  }
  .brand-block {
    position: absolute;
    left: 60px;
    top: 160px;
    width: 390px;
    text-align: center;
    color: var(--navy);
  }
  .brand-mark {
    display: block;
    width: 34px;
    height: 34px;
    margin: 0 auto 22px;
    background: var(--navy);
  }
  .brand-name {
    font-family: "Noto Serif", serif;
    font-weight: 400;
    font-size: 54px;
    line-height: 1.1;
    letter-spacing: 1px;
    text-transform: uppercase;
  }
  .contact-block {
    position: absolute;
    left: 512px;
    top: 140px;
    font-family: "Roboto", sans-serif;
    color: var(--text-grey);
  }
  .person-name {
    font-family: "Noto Serif", serif;
    font-weight: 400;
    font-size: 38px;
    color: var(--navy);
    letter-spacing: 0.5px;
    text-transform: uppercase;
    line-height: 1;
  }
  .person-title {
    font-size: 25px;
    font-weight: 400;
    margin-top: 12px;
  }
  .mailing-address {
    font-size: 25px;
    font-weight: 300;
    line-height: 42px;
    margin-top: 28px;
  }
  .contact-line {
    display: flex;
    align-items: center;
    font-size: 25px;
    font-weight: 300;
    height: 40px;
  }
  .contact-line:first-of-type { margin-top: 8px; }
  .contact-icon {
    width: 22px;
    height: 22px;
    margin: 0 28px 0 10px;
    fill: var(--navy);
  }
  .website {
    position: absolute;
    left: 512px;
    top: 548px;
    font-family: "Roboto", sans-serif;
    font-size: 25px;
    font-weight: 400;
    color: var(--white);
  }
</style>
</head>
<body>
  <div class="business-card">
    <svg class="card-band" width="1000" height="604" viewBox="0 0 1000 604" aria-hidden="true">
      <rect x="0" y="580" width="440" height="24" fill="var(--stripe-grey)" opacity="0.7"/>
      <path d="M 403 604 L 440 542 Q 447 531 462 531 L 1000 531 L 1000 604 Z" fill="var(--navy)"/>
    </svg>

    <div class="brand-block">
      <span class="brand-mark"></span>
      <div class="brand-name">Verdant<br>Systems</div>
    </div>

    <div class="contact-block">
      <div class="person-name">Naomi Trelvik</div>
      <div class="person-title">Customer Relationship Specialist</div>
      <div class="mailing-address">234 Anywhere St., Any City,<br>Any Town, US 123456</div>
      <div class="contact-line">
        <svg class="contact-icon" viewBox="0 0 24 24" aria-hidden="true">
          <path d="M3 9c0-3 4-5 9-5s9 2 9 5v1h-5V8H8v2H3z"/>
          <path d="M6 11h12l2 9H4z"/>
        </svg>
        <span>111-111-1111</span>
      </div>
      <div class="contact-line">
        <svg class="contact-icon" viewBox="0 0 24 24" aria-hidden="true">
          <path d="M2 5h20v14H2z M4 7v1l8 5 8-5V7l-8 5z" fill-rule="evenodd"/>
        </svg>
        <span>naomi.t@verdantsystems.com</span>
      </div>
    </div>

    <div class="website">www.verdantsystems.com</div>
  </div>
</body>
</html>
```